Retail Seafood business needs package/label design

In need of packaging/label design for multiple seafood products such as sword fish, halibut, cod fish, scallops, mahi, catfish, and lobster tails

```html
<!DOCTYPE html>
<html lang="en">
<head>
<meta charset="UTF-8">
<title>Ocean Fish Fillets – Dorado Tin Label</title>
<link href="https://fonts.googleapis.com/css2?family=Montserrat:wght@400;700;800&family=Bebas+Neue&family=Yellowtail&display=swap" rel="stylesheet">
<style>
  :root {
    --page: #ffffff;
    --tin-gold: #e9cf86;
    --tin-gold-dark: #d6b865;
    --lid-cream: #f9f5ec;
    --teal: #36716f;
    --teal-ink: #2e6a69;
    --mint: #5cc58a;
    --mint-soft: #a9e2bf;
    --butter: #f7e4a6;
    --steel: #c9c9c9;
    --steel-dark: #a9a9a9;
    --white: #ffffff;
  }
  * { margin: 0; padding: 0; box-sizing: border-box; }
  html, body { width: 1200px; height: 1200px; overflow: hidden; background: var(--page); }
  .canvas { position: relative; width: 1200px; height: 1200px; }
  .lid-art { position: absolute; inset: 0; }
  .label-text { position: absolute; white-space: nowrap; }
  .tagline-original {
    left: 455px; top: 368px;
    font-family: "Yellowtail", cursive; font-size: 44px; color: var(--mint);
  }
  .product-line {
    left: 455px; top: 440px;
    font-family: "Montserrat", sans-serif; font-weight: 800; font-size: 39px;
    line-height: 50px; letter-spacing: 2.5px; color: var(--teal-ink);
  }
  .quality-line {
    left: 456px; top: 608px;
    font-family: "Montserrat", sans-serif; font-weight: 700; font-size: 19px;
    letter-spacing: 2.2px; color: var(--white);
  }
  .species-name {
    left: 454px; top: 636px;
    font-family: "Bebas Neue", sans-serif; font-size: 96px; line-height: 90px;
    letter-spacing: 3px; color: var(--mint);
  }
  .product-copy {
    left: 455px; top: 729px;
    font-family: "Montserrat", sans-serif; font-weight: 400; font-size: 11.6px;
    line-height: 14.6px; color: var(--white);
  }
  .natural-claim {
    left: 455px; top: 792px;
    font-family: "Yellowtail", cursive; font-size: 30px; color: var(--mint);
  }
  .closing-line {
    left: 455px; top: 865px;
    font-family: "Montserrat", sans-serif; font-weight: 700; font-size: 20px;
    letter-spacing: 2.4px; color: var(--teal-ink);
  }
  .pull-tab { position: absolute; left: 0; top: 0; }
</style>
</head>
<body>
<div class="canvas">
  <svg class="lid-art" width="1200" height="1200" viewBox="0 0 1200 1200">
    <defs>
      <linearGradient id="tinRim" x1="0" y1="0" x2="0" y2="1">
        <stop offset="0" stop-color="var(--tin-gold)"/>
        <stop offset="1" stop-color="var(--tin-gold-dark)"/>
      </linearGradient>
      <linearGradient id="fishTone" x1="0" y1="0" x2="0" y2="1">
        <stop offset="0" stop-color="var(--mint)" stop-opacity="0.55"/>
        <stop offset="1" stop-color="var(--mint-soft)" stop-opacity="0.45"/>
      </linearGradient>
      <clipPath id="lidFace">
        <rect x="156" y="287" width="888" height="626" rx="100"/>
      </clipPath>
    </defs>
    <rect class="tin-rim" x="137" y="268" width="926" height="664" rx="118" fill="url(#tinRim)"/>
    <rect class="lid-face" x="156" y="287" width="888" height="626" rx="100" fill="var(--lid-cream)"/>
    <g clip-path="url(#lidFace)">
      <path class="fish-illustration" role="img" aria-label="Hand-engraved sketch of a dorado fish, head up, in mint green line work"
            d="M300 345 C340 330 390 380 410 450 C450 560 470 680 430 790 C410 850 380 900 340 913 L210 913 C190 850 180 760 185 660 C190 540 230 400 300 345 Z"
            fill="url(#fishTone)"/>
      <rect class="band-title" x="427" y="361" width="640" height="59" fill="var(--teal)"/>
      <rect class="band-highlight" x="940" y="528" width="120" height="147" fill="var(--butter)"/>
      <rect class="band-product" x="427" y="594" width="640" height="246" fill="var(--teal)"/>
    </g>
    <circle class="stamp-badge" cx="777" cy="497" r="36" fill="none" stroke="var(--mint)" stroke-width="2.5"/>
    <circle class="stamp-badge-inner" cx="777" cy="497" r="20" fill="none" stroke="var(--mint)" stroke-width="1.5"/>
  </svg>

  <div class="label-text tagline-original">the Original</div>
  <div class="label-text product-line">OCEAN FISH<br>FILLETS</div>
  <div class="label-text quality-line">PREMIUM QUALITY</div>
  <div class="label-text species-name">DORADO</div>
  <div class="label-text product-copy">Lorem ipsum dolor sit amet, consectetuer adipiscing elit.<br>Cum sociis natoque penatibus et magnis dis parturient<br>montes, nascetur ridiculus mus. Donec quam felis, ultricies<br>nec, pellentesque eu, pretium quis, sem.</div>
  <div class="label-text natural-claim">100% Natural Product</div>
  <div class="label-text closing-line">PERFECT CHOICE!</div>

  <svg class="pull-tab" width="1200" height="1200" viewBox="0 0 1200 1200">
    <defs>
      <linearGradient id="steel" x1="0" y1="0" x2="0" y2="1">
        <stop offset="0" stop-color="#e2e2e2"/>
        <stop offset="1" stop-color="var(--steel-dark)"/>
      </linearGradient>
      <mask id="ringHole">
        <rect width="1200" height="1200" fill="#fff"/>
        <circle cx="817" cy="598" r="62" fill="#000"/>
      </mask>
    </defs>
    <rect x="740" y="520" width="285" height="158" rx="79" fill="url(#steel)" stroke="var(--steel-dark)" stroke-width="2" mask="url(#ringHole)"/>
    <circle cx="817" cy="598" r="62" fill="none" stroke="var(--steel-dark)" stroke-width="2"/>
    <circle cx="961" cy="598" r="30" fill="#dcdcdc" stroke="var(--steel-dark)" stroke-width="2"/>
    <circle cx="961" cy="598" r="18" fill="var(--steel)"/>
  </svg>
</div>
</body>
</html>
```